Oak Ridge Ways Home Page

Redesign the home page -- make it look more attractive and inviting.
Do we need to cut down on the wording? Probably -
Want a cleaner design.
Can go to www.OakRidgeWays.org for the website

```html
<!DOCTYPE html>
<html lang="en">
<head>
<meta charset="utf-8">
<title>Oak Ridge Ways – Home Page</title>
<link href="https://fonts.googleapis.com/css2?family=Poppins:ital,wght@0,400;0,500;0,600;0,700;0,800;1,400&display=swap" rel="stylesheet">
<style>
:root{
  --blue:#1428d4;
  --green:#08cc7c;
  --ink:#1428d4;
  --grey:#6b6f86;
  --stage:#e9eaee;
  --white:#ffffff;
}
*{margin:0;padding:0;box-sizing:border-box}
html,body{width:1200px;height:2213px;overflow:hidden}
body{background:var(--stage);font-family:'Poppins',sans-serif;position:relative;color:var(--grey)}
.page{position:absolute;top:63px;width:502px;height:2062px;background:var(--white);overflow:hidden;box-shadow:0 6px 24px rgba(20,30,80,.12)}
.page--video{left:64px}
.page--art{left:619px}
.page-bg{position:absolute;inset:0}
.abs{position:absolute}

/* header */
.brand{left:24px;top:18px;display:flex;align-items:center;gap:6px;font-size:11px;font-weight:500;color:var(--white)}
.brand-mark{width:16px;height:16px;background:var(--white);border-radius:3px}
.nav{left:176px;top:23px;display:flex;gap:16px;font-size:6.5px;font-weight:500;color:var(--white)}
.nav .active{color:var(--green)}
.nav-icons{left:392px;top:20px;display:flex;gap:8px;align-items:center}
.login{left:436px;top:19px;width:50px;height:17px;border-radius:9px;background:var(--green);color:var(--white);font-size:6px;font-weight:600;display:flex;align-items:center;justify-content:center}

/* hero */
.hero-kicker{left:63px;top:109px;font-size:9.5px;color:var(--white)}
.hero-title{left:63px;top:122px;font-size:14.5px;line-height:17.5px;font-weight:700;color:var(--white)}
.hero-sub{left:63px;top:157px;font-size:7.5px;color:var(--white)}
.btn{border-radius:10px;font-size:6px;font-weight:700;display:flex;align-items:center;justify-content:center;text-transform:uppercase;letter-spacing:.1px}
.btn--green{background:var(--green);color:var(--white)}
.btn--blue{background:var(--blue);color:var(--white)}
.hero-btn{left:63px;top:180px;width:83px;height:20px}
.hero-note{left:63px;top:216px;font-size:5.3px;line-height:6.6px;font-style:italic;color:var(--white)}
.hero-video{left:243px;top:75px;width:259px;height:150px;border-radius:80px 0 0 80px;background:linear-gradient(120deg,#f4f4f4,#d9d9d9)}
.play{left:135px;top:52px;width:40px;height:40px;border-radius:50%;background:var(--white);box-shadow:0 3px 10px rgba(0,0,0,.15);display:flex;align-items:center;justify-content:center}
.video-bar{left:20px;right:6px;bottom:10px;height:14px;font-size:5px;color:#fff;display:flex;align-items:center;gap:6px}
.video-bar .track{flex:1;height:2px;background:rgba(255,255,255,.6)}
.hero-caption{left:322px;top:231px;width:160px;font-size:5px;line-height:6.5px;text-align:center;color:var(--white)}
.hero-art{left:246px;top:70px;width:240px;height:160px;border-radius:30px;background:radial-gradient(circle at 30% 60%,#19d48a 0,#12b77a 35%,rgba(246,185,40,.55) 60%,rgba(20,40,212,0) 75%)}

/* pricing */
.plan{top:343px;width:179px;height:252px;border-radius:12px;text-align:center;color:var(--white)}
.plan--silver{left:63px;background:var(--blue)}
.plan--gold{left:258px;background:var(--green)}
.plan h3{margin-top:13px;font-size:14px;font-weight:700}
.plan .desc{margin:3px auto 0;width:150px;font-size:6px;line-height:8px}
.price{margin-top:8px;font-size:17px;font-weight:800;letter-spacing:.5px}
.price sup{font-size:9px}
.plan--silver .price{color:var(--green)}
.plan--gold .price{color:var(--blue)}
.divider{margin:8px 0 0;border-top:1px dashed rgba(255,255,255,.35)}
.get{margin-top:9px;font-size:6.3px;font-weight:700}
.plan ul{list-style:none;margin-top:9px}
.plan li{font-size:5.8px;line-height:7.5px;margin-bottom:8px;padding:0 18px}
.plan li::before{content:"✓ ";font-weight:700}
.plan .btn{position:absolute;left:42px;top:217px;width:96px;height:20px}

/* features */
.step{width:23px;height:23px;border-radius:50%;background:var(--green);color:var(--white);font-size:8px;font-weight:700;display:flex;align-items:center;justify-content:center}
.feat-title{font-size:9px;line-height:11.5px;font-weight:700;color:var(--ink)}
.feat-list{list-style:none;width:196px}
.feat-list li{position:relative;padding-left:16px;font-size:6.3px;line-height:7.8px;margin-bottom:10px}
.feat-list li::before{content:"";position:absolute;left:0;top:1px;width:9px;height:9px;border-radius:50%;background:var(--blue)}
.feat-list li::after{content:"";position:absolute;left:2.6px;top:3px;width:3px;height:2px;border-left:1.3px solid #fff;border-bottom:1.3px solid #fff;transform:rotate(-45deg)}
.read{width:63px;height:19px}
.illus{border-radius:24px;background:linear-gradient(135deg,rgba(8,204,124,.28),rgba(20,40,212,.14) 60%,rgba(246,185,40,.25))}

/* testimonials */
.reviews-title{left:0;width:502px;top:1640px;text-align:center;font-size:11.5px;font-weight:700;color:var(--white)}
.review{top:1675px;width:118px;height:112px;background:var(--white);border-radius:14px;padding:12px 12px 0 13px}
.quote-mark{font-size:14px;font-weight:800;color:var(--green);line-height:10px}
.review p{margin-top:5px;font-size:5px;line-height:6.4px;font-style:italic;color:var(--grey)}
.review .who{position:absolute;left:13px;bottom:14px;font-size:6.5px;font-weight:700;color:var(--ink)}
.arrow{top:1728px;width:14px;height:10px}

/* footer */
.foot-brand{left:0;width:502px;top:1908px;display:flex;justify-content:center;align-items:center;gap:7px;font-size:11.5px;font-weight:500;color:var(--white)}
.foot-brand .brand-mark{width:20px;height:20px}
.contact{top:1955px;display:flex;gap:7px;align-items:center;color:var(--white);font-size:6px;line-height:8px}
.contact .ico{width:18px;height:18px;border-radius:50%;background:rgba(255,255,255,.9);display:flex;align-items:center;justify-content:center}
.foot-rule{left:69px;width:365px;top:1993px;border-top:1px solid var(--green)}
.copyright{left:0;width:502px;top:2009px;text-align:center;font-size:6px;color:var(--white)}
.social{left:0;width:502px;top:2034px;display:flex;justify-content:center;gap:10px}
.social span{width:10px;height:10px;border-radius:50%;background:var(--white)}
</style>
</head>
<body>

<!-- ================= Variant A: video hero ================= -->
<main class="page page--video">
  <svg class="page-bg" width="502" height="2062" viewBox="0 0 502 2062">
    <defs>
      <linearGradient id="mistA" x1="0" y1="0" x2="0" y2="1">
        <stop offset="0" stop-color="#f4f5fb"/><stop offset=".7" stop-color="#f2f4fa"/><stop offset="1" stop-color="#dcf3ec"/>
      </linearGradient>
    </defs>
    <path d="M0 0H502V282C430 270 340 262 255 282C160 304 70 316 0 311Z" fill="#1428d4"/>
    <path d="M0 690C120 692 210 660 310 650C400 642 470 648 502 645V1570H0Z" fill="url(#mistA)"/>
    <path d="M0 1552C90 1590 200 1592 300 1572C400 1552 460 1532 502 1518V2062H0Z" fill="#08cc7c"/>
    <path d="M0 1853C120 1878 250 1880 360 1862C430 1850 480 1840 502 1832V2062H0Z" fill="#1428d4"/>
  </svg>

  <div class="abs brand"><span class="brand-mark"></span>Oak Ridge Ways</div>
  <nav class="abs nav"><span class="active">Home</span><span>Testimonials</span><span>Max Scores</span><span>FAQ</span><span>Blog</span></nav>
  <div class="abs nav-icons">
    <svg width="9" height="9" viewBox="0 0 10 10"><circle cx="4" cy="4" r="3" fill="none" stroke="#fff" stroke-width="1.3"/><path d="M6.3 6.3L9 9" stroke="#fff" stroke-width="1.3"/></svg>
    <svg width="15" height="15" viewBox="0 0 16 16"><circle cx="8" cy="8" r="7" fill="none" stroke="#08cc7c" stroke-width="1"/><path d="M5.5 5c0 3 2.5 5.5 5.5 5.5l.6-1.4-1.6-.8-.8.8C8 8.6 7.4 8 7 6.9l.8-.8L7 4.5z" fill="#08cc7c"/></svg>
  </div>
  <div class="abs login">LOGIN</div>

  <div class="abs hero-kicker">Recognized as</div>
  <h1 class="abs hero-title">The BEST Credit Score<br>Improvement Program</h1>
  <div class="abs hero-sub">81 Average Point Improvement</div>
  <div class="abs btn btn--green hero-btn">Get Started Here</div>
  <p class="abs hero-note">Requesting Your Lender's Credit Report<br>Thru Oak Ridge Ways Does Not Lower<br>Your Credit Scores</p>

  <div class="abs hero-video" role="img" aria-label="Explainer video still: a hand sketching a figure with a marker">
    <div class="abs play"><svg width="40" height="40" viewBox="0 0 40 40"><circle cx="20" cy="20" r="15" fill="#1428d4"/><path d="M16 12.5L27 20 16 27.5z" fill="#08cc7c"/></svg></div>
    <div class="abs video-bar"><span>0:00 / 1:02</span><span class="track"></span><span>◂)</span></div>
  </div>
  <p class="abs hero-caption">Harbor Lane Financial is a 501 (c)(3) Non-Profit Certified Credit Counselor which manages Oak Ridge Ways</p>

  <section class="abs plan plan--silver">
    <h3>Silver</h3>
    <p class="desc">Lender's Report, Lender's<br>Scores &amp; Analysis</p>
    <div class="price"><sup>$</sup>59.95</div>
    <div class="divider"></div>
    <div class="get">Get Your . . .</div>
    <ul><li>ScoreMark® Credit Scores Lenders use</li><li>Complete Credit Score Analysis</li><li>Potential Mortgage and Auto<br>Loan Qualifications</li></ul>
    <div class="btn btn--green">Get Started Here</div>
  </section>
  <section class="abs plan plan--gold">
    <h3>Gold</h3>
    <p class="desc">Lender's Report, Lender's Scores, Analysis<br>&amp; Steps to Score Improvement</p>
    <div class="price"><sup>$</sup>79.95</div>
    <div class="divider"></div>
    <div class="get">Get Your . . .</div>
    <ul><li>ScoreMark® Credit Scores Lenders use</li><li>Complete Credit Score Analysis</li><li>Potential Mortgage and Auto<br>Loan Qualifications</li><li>Personalized Solutions to Higher<br>ScoreMark® Credit Scores</li></ul>
    <div class="btn btn--blue">Get Started Here</div>
  </section>

  <!-- 01 -->
  <div class="abs step" style="left:63px;top:726px">01</div>
  <h2 class="abs feat-title" style="left:96px;top:728px;width:168px">See What Your Lenders See - Get the Same Credit Report and Scores Lenders Use</h2>
  <ul class="abs feat-list" style="left:63px;top:780px"><li>As a Certified Credit Counselor, We Provide the Same Credit Report and 3 Scores Used by Mortgage &amp; Auto Lenders</li><li>Don't be Misled by "Unreliable Internet Credit Scores" - Not Knowing Accurate Scores could Cost You Lots of Money</li></ul>
  <div class="abs btn btn--green read" style="left:63px;top:852px">Read More</div>
  <div class="abs illus" style="left:280px;top:715px;width:182px;height:150px" role="img" aria-label="Illustration: two people beside large phones showing a credit card and a coin"></div>

  <!-- 02 -->
  <div class="abs illus" style="left:47px;top:925px;width:163px;height:144px" role="img" aria-label="Illustration: a man next to a phone with a card, a check mark and a gold coin"></div>
  <div class="abs step" style="left:237px;top:939px">02</div>
  <h2 class="abs feat-title" style="left:269px;top:941px;width:190px">Work with the BEST Credit Score Improvement Program</h2>
  <ul class="abs feat-list" style="left:237px;top:984px"><li>Oak Ridge Ways Averages an Amazing 81-Point Improvement for all 3 ScoreMark Credit Scores</li><li>Identifies Accounts to Pay Down (by Priority), to Close, to Use, to Open, to Refinance, and to Consolidate</li></ul>
  <div class="abs btn btn--green read" style="left:237px;top:1049px">Read More</div>

  <!-- 03 -->
  <div class="abs step" style="left:63px;top:1143px">03</div>
  <h2 class="abs feat-title" style="left:96px;top:1145px;width:160px">Want to Know Your Potential Mortgage and Auto Loan Qualifications</h2>
  <ul class="abs feat-list" style="left:63px;top:1198px;width:200px"><li>Since We Provide the Same ScoreMark Scores Lenders Use, We Give You Insight to Your Loan Qualifications</li><li>See What Mortgage and Auto Loan Options Work Best for you. Don't Wait for a Loan Officer</li></ul>
  <div class="abs btn btn--green read" style="left:63px;top:1257px">Read More</div>
  <div class="abs illus" style="left:276px;top:1127px;width:186px;height:172px" role="img" aria-label="Illustration: two people with coins around a phone showing cash and a check mark"></div>

  <!-- 04 -->
  <div class="abs illus" style="left:56px;top:1346px;width:167px;height:137px" role="img" aria-label="Illustration: a woman holding a card beside a phone with the brand name"></div>
  <div class="abs step" style="left:237px;top:1354px">04</div>
  <h2 class="abs feat-title" style="left:269px;top:1356px;width:195px">Improve Your Purchasing Power by Increasing Your Lender's ScoreMark Scores</h2>
  <ul class="abs feat-list" style="left:237px;top:1398px;width:205px"><li>Loan Officers Don't Care if You are Paying $100's More on Your Mortgage or Auto Loan Payment - You're Paying It!</li><li>Most Home and Auto Buyers have Higher Payments because of Less-than-Excellent ScoreMark Scores - Usually Less than 760</li></ul>
  <div class="abs btn btn--green read" style="left:237px;top:1470px">Read More</div>

  <h2 class="abs reviews-title">What people will tell you about us</h2>
  <svg class="abs arrow" style="left:50px" viewBox="0 0 14 10"><path d="M13 5H1M5 1L1 5l4 4" fill="none" stroke="#1428d4" stroke-width="1"/></svg>
  <article class="abs review" style="left:63px"><div class="quote-mark">“</div><p>"I went to one of the credit bureau's websites and the score offered there was over 60 points higher than what my lender had my score at. I discovered my lender uses the same credit scores found here."</p><div class="who">Leo P.</div></article>
  <article class="abs review" style="left:192px"><div class="quote-mark">“</div><p>My score increased 110 points after 33 days (through Oak Ridge Ways). It is pretty cool and exciting to see my credit score (s) go up. I just bought my home."</p><div class="who">Nora W.</div></article>
  <article class="abs review" style="left:321px"><div class="quote-mark">“</div><p>"I am ready to buy my home. I will recommend this service to anyone needing help with credit. It is well worth the money."</p><div class="who">Ruth K.</div></article>
  <svg class="abs arrow" style="left:442px" viewBox="0 0 14 10"><path d="M1 5h12M9 1l4 4-4 4" fill="none" stroke="#1428d4" stroke-width="1"/></svg>

  <div class="abs foot-brand"><span class="brand-mark"></span>Oak Ridge Ways</div>
  <div class="abs contact" style="left:73px"><span class="ico"><svg width="8" height="8" viewBox="0 0 10 10"><path d="M2 1c0 4 3 8 7 8l.6-2-2-1-1 1C5.3 6.6 3.8 5 3.2 3.5l1-1-1-2z" fill="#08cc7c"/></svg></span><span>Phone<br>(555) 014-2270</span></div>
  <div class="abs contact" style="left:183px"><span class="ico"><svg width="8" height="9" viewBox="0 0 10 12"><path d="M5 11C2 7 1 5.5 1 4a4 4 0 018 0c0 1.5-1 3-4 7z" fill="#08cc7c"/><circle cx="5" cy="4" r="1.4" fill="#fff"/></svg></span><span>18 Linden Court, Suite 210,<br>Fairhaven, Wyoming 82000</span></div>
  <div class="abs contact" style="left:326px"><span class="ico"><svg width="8" height="7" viewBox="0 0 10 8"><rect x=".5" y=".5" width="9" height="7" fill="#08cc7c"/><path d="M.5 .8L5 4.5 9.5.8" fill="none" stroke="#fff" stroke-width=".9"/></svg></span><span>Email<br>hello@oakridgeways.org</span></div>
  <div class="abs foot-rule"></div>
  <p class="abs copyright">Copyright 2022 by Oak Ridge Ways. Terms Of Use &nbsp;| &nbsp;Privacy Statement</p>
  <div class="abs social"><span></span><span></span><span></span></div>
</main>

<!-- ================= Variant B: illustrated hero ================= -->
<main class="page page--art">
  <svg class="page-bg" width="502" height="2062" viewBox="0 0 502 2062">
    <defs>
      <linearGradient id="mistB" x1="0" y1="0" x2="0" y2="1">
        <stop offset="0" stop-color="#f4f5fb"/><stop offset=".7" stop-color="#f2f4fa"/><stop offset="1" stop-color="#dcf3ec"/>
      </linearGradient>
    </defs>
    <path d="M0 0H502V282C430 270 340 262 255 282C160 304 70 316 0 311Z" fill="#1428d4"/>
    <path d="M0 690C120 692 210 660 310 650C400 642 470 648 502 645V1570H0Z" fill="url(#mistB)"/>
    <path d="M0 1552C90 1590 200 1592 300 1572C400 1552 460 1532 502 1518V2062H0Z" fill="#08cc7c"/>
    <path d="M0 1853C120 1878 250 1880 360 1862C430 1850 480 1840 502 1832V2062H0Z" fill="#1428d4"/>
  </svg>

  <div class="abs brand"><span class="brand-mark"></span>Oak Ridge Ways</div>
  <nav class="abs nav"><span class="active">Home</span><span>Testimonials</span><span>Max Scores</span><span>FAQ</span><span>Blog</span></nav>
  <div class="abs nav-icons">
    <svg width="9" height="9" viewBox="0 0 10 10"><circle cx="4" cy="4" r="3" fill="none" stroke="#fff" stroke-width="1.3"/><path d="M6.3 6.3L9 9" stroke="#fff" stroke-width="1.3"/></svg>
    <svg width="15" height="15" viewBox="0 0 16 16"><circle cx="8" cy="8" r="7" fill="none" stroke="#08cc7c" stroke-width="1"/><path d="M5.5 5c0 3 2.5 5.5 5.5 5.5l.6-1.4-1.6-.8-.8.8C8 8.6 7.4 8 7 6.9l.8-.8L7 4.5z" fill="#08cc7c"/></svg>
  </div>
  <div class="abs login">LOGIN</div>

  <div class="abs hero-kicker">Recognized as</div>
  <h1 class="abs hero-title">The BEST Credit Score<br>Improvement Program</h1>
  <div class="abs hero-sub">81 Average Point Improvement</div>
  <div class="abs btn btn--green hero-btn">Get Started Here</div>
  <p class="abs hero-note">Requesting Your Lender's Credit Report<br>Thru Oak Ridge Ways Does Not Lower<br>Your Credit Scores</p>

  <div class="abs hero-art" role="img" aria-label="Illustration: a green wallet, gold coins and a person beside a large phone, with a video play button">
    <div class="abs play" style="left:78px;top:66px;background:rgba(255,255,255,.35)"><svg width="40" height="40" viewBox="0 0 40 40"><circle cx="20" cy="20" r="15" fill="#1428d4"/><path d="M16 12.5L27 20 16 27.5z" fill="#08cc7c"/></svg></div>
  </div>

  <section class="abs plan plan--silver">
    <h3>Silver</h3>
    <p class="desc">Lender's Report, Lender's<br>Scores &amp; Analysis</p>
    <div class="price"><sup>$</sup>59.95</div>
    <div class="divider"></div>
    <div class="get">Get Your . . .</div>
    <ul><li>ScoreMark® Credit Scores Lenders use</li><li>Complete Credit Score Analysis</li><li>Potential Mortgage and Auto<br>Loan Qualifications</li></ul>
    <div class="btn btn--green">Get Started Here</div>
  </section>
  <section class="abs plan plan--gold">
    <h3>Gold</h3>
    <p class="desc">Lender's Report, Lender's Scores, Analysis<br>&amp; Steps to Score Improvement</p>
    <div class="price"><sup>$</sup>79.95</div>
    <div class="divider"></div>
    <div class="get">Get Your . . .</div>
    <ul><li>ScoreMark® Credit Scores Lenders use</li><li>Complete Credit Score Analysis</li><li>Potential Mortgage and Auto<br>Loan Qualifications</li><li>Personalized Solutions to Higher<br>ScoreMark® Credit Scores</li></ul>
    <div class="btn btn--blue">Get Started Here</div>
  </section>

  <div class="abs step" style="left:63px;top:726px">01</div>
  <h2 class="abs feat-title" style="left:96px;top:728px;width:168px">See What Your Lenders See - Get the Same Credit Report and Scores Lenders Use</h2>
  <ul class="abs feat-list" style="left:63px;top:780px"><li>As a Certified Credit Counselor, We Provide the Same Credit Report and 3 Scores Used by Mortgage &amp; Auto Lenders</li><li>Don't be Misled by "Unreliable Internet Credit Scores" - Not Knowing Accurate Scores could Cost You Lots of Money</li></ul>
  <div class="abs btn btn--green read" style="left:63px;top:852px">Read More</div>
  <div class="abs illus" style="left:280px;top:715px;width:182px;height:150px" role="img" aria-label="Illustration: two people beside large phones showing a credit card and a coin"></div>

  <div class="abs illus" style="left:47px;top:925px;width:163px;height:144px" role="img" aria-label="Illustration: a man next to a phone with a card, a check mark and a gold coin"></div>
  <div class="abs step" style="left:237px;top:939px">02</div>
  <h2 class="abs feat-title" style="left:269px;top:941px;width:190px">Work with the BEST Credit Score Improvement Program</h2>
  <ul class="abs feat-list" style="left:237px;top:984px"><li>Oak Ridge Ways Averages an Amazing 81-Point Improvement for all 3 ScoreMark Credit Scores</li><li>Identifies Accounts to Pay Down (by Priority), to Close, to Use, to Open, to Refinance, and to Consolidate</li></ul>
  <div class="abs btn btn--green read" style="left:237px;top:1049px">Read More</div>

  <div class="abs step" style="left:63px;top:1143px">03</div>
  <h2 class="abs feat-title" style="left:96px;top:1145px;width:160px">Want to Know Your Potential Mortgage and Auto Loan Qualifications</h2>
  <ul class="abs feat-list" style="left:63px;top:1198px;width:200px"><li>Since We Provide the Same ScoreMark Scores Lenders Use, We Give You Insight to Your Loan Qualifications</li><li>See What Mortgage and Auto Loan Options Work Best for you. Don't Wait for a Loan Officer</li></ul>
  <div class="abs btn btn--green read" style="left:63px;top:1257px">Read More</div>
  <div class="abs illus" style="left:276px;top:1127px;width:186px;height:172px" role="img" aria-label="Illustration: two people with coins around a phone showing cash and a check mark"></div>

  <div class="abs illus" style="left:56px;top:1346px;width:167px;height:137px" role="img" aria-label="Illustration: a woman holding a card beside a phone with the brand name"></div>
  <div class="abs step" style="left:237px;top:1354px">04</div>
  <h2 class="abs feat-title" style="left:269px;top:1356px;width:195px">Improve Your Purchasing Power by Increasing Your Lender's ScoreMark Scores</h2>
  <ul class="abs feat-list" style="left:237px;top:1398px;width:205px"><li>Loan Officers Don't Care if You are Paying $100's More on Your Mortgage or Auto Loan Payment - You're Paying It!</li><li>Most Home and Auto Buyers have Higher Payments because of Less-than-Excellent ScoreMark Scores - Usually Less than 760</li></ul>
  <div class="abs btn btn--green read" style="left:237px;top:1470px">Read More</div>

  <h2 class="abs reviews-title">What people will tell you about us</h2>
  <svg class="abs arrow" style="left:50px" viewBox="0 0 14 10"><path d="M13 5H1M5 1L1 5l4 4" fill="none" stroke="#1428d4" stroke-width="1"/></svg>
  <article class="abs review" style="left:63px"><div class="quote-mark">“</div><p>"I went to one of the credit bureau's websites and the score offered there was over 60 points higher than what my lender had my score at. I discovered my lender uses the same credit scores found here."</p><div class="who">Leo P.</div></article>
  <article class="abs review" style="left:192px"><div class="quote-mark">“</div><p>My score increased 110 points after 33 days (through Oak Ridge Ways). It is pretty cool and exciting to see my credit score (s) go up. I just bought my home."</p><div class="who">Nora W.</div></article>
  <article class="abs review" style="left:321px"><div class="quote-mark">“</div><p>"I am ready to buy my home. I will recommend this service to anyone needing help with credit. It is well worth the money."</p><div class="who">Ruth K.</div></article>
  <svg class="abs arrow" style="left:442px" viewBox="0 0 14 10"><path d="M1 5h12M9 1l4 4-4 4" fill="none" stroke="#1428d4" stroke-width="1"/></svg>

  <div class="abs foot-brand"><span class="brand-mark"></span>Oak Ridge Ways</div>
  <div class="abs contact" style="left:73px"><span class="ico"><svg width="8" height="8" viewBox="0 0 10 10"><path d="M2 1c0 4 3 8 7 8l.6-2-2-1-1 1C5.3 6.6 3.8 5 3.2 3.5l1-1-1-2z" fill="#08cc7c"/></svg></span><span>Phone<br>(555) 014-2270</span></div>
  <div class="abs contact" style="left:183px"><span class="ico"><svg width="8" height="9" viewBox="0 0 10 12"><path d="M5 11C2 7 1 5.5 1 4a4 4 0 018 0c0 1.5-1 3-4 7z" fill="#08cc7c"/><circle cx="5" cy="4" r="1.4" fill="#fff"/></svg></span><span>18 Linden Court, Suite 210,<br>Fairhaven, Wyoming 82000</span></div>
  <div class="abs contact" style="left:326px"><span class="ico"><svg width="8" height="7" viewBox="0 0 10 8"><rect x=".5" y=".5" width="9" height="7" fill="#08cc7c"/><path d="M.5 .8L5 4.5 9.5.8" fill="none" stroke="#fff" stroke-width=".9"/></svg></span><span>Email<br>hello@oakridgeways.org</span></div>
  <div class="abs foot-rule"></div>
  <p class="abs copyright">Copyright 2022 by Oak Ridge Ways. Terms Of Use &nbsp;| &nbsp;Privacy Statement</p>
  <div class="abs social"><span></span><span></span><span></span></div>
</main>

</body>
</html>
```